Business card for Luxury Portable Restroom Trailer company

We are a Luxury Portable Restroom Trailer Company Called FALCRIDGE HIRES. Based in Orange County California. We provide portable restroom trailers for events, such as, Weddings, Concerts, Charity events, Sporting events, Tournaments, Corporate events, ect. We rent and Sell the Luxury restrooms. Our colors are white, grey, and Orange. As you will see in the logo we uploaded.
There are 2 people in the company so the names and titles will change for the 3 people but card will remain the same. Here is the information for each Person: Dwight Penner CFO 555 318-0476
next Person: Leon Marchetti VP 555 318-0476
Next Person: Owen Marchetti CEO 555 318-0476
Information to include on the card: Luxury Restroom Trailers Rental and Sales. Weddings, Concerts, Charity, Sporting and Corp. Events.

```html
<!DOCTYPE html>
<html lang="en">
<head>
<meta charset="utf-8">
<title>Falcridge Hires – Business Card</title>
<link rel="stylesheet" href="https://fonts.googleapis.com/css2?family=Open+Sans:wght@400;600;700&display=swap">
<style>
  :root {
    --stage: #242424;
    --card-dark: #222225;
    --orange: #f26a22;
    --orange-deep: #b9501a;
    --grey: #6d6e71;
    --white: #f4f4f4;
  }
  * { margin: 0; padding: 0; box-sizing: border-box; }
  html, body {
    width: 1200px; height: 768px; overflow: hidden;
    background: var(--stage);
    font-family: "Open Sans", Arial, sans-serif;
  }
  .stage {
    position: relative; width: 1200px; height: 768px;
    display: flex; align-items: center; justify-content: center; gap: 60px;
  }
  .card {
    position: relative; width: 510px; height: 292px; overflow: hidden;
    box-shadow: 0 10px 30px rgba(0,0,0,.45);
  }
  /* front */
  .card--front { background: var(--card-dark); }
  .brand {
    position: absolute; display: flex; align-items: center; gap: 8px;
    font-weight: 700; letter-spacing: .04em; white-space: nowrap; z-index: 2;
  }
  .card--front .brand { top: 30px; left: 190px; font-size: 24px; color: var(--orange); }
  .brand__mark { width: 12px; height: 12px; background: currentColor; flex: none; }
  .services {
    position: absolute; top: 96px; left: 26px; list-style: none; z-index: 2;
    font-size: 11.5px; line-height: 17px; color: var(--white); white-space: nowrap;
  }
  .services li { display: flex; align-items: center; gap: 7px; }
  .services li::before {
    content: ""; width: 6px; height: 6px; background: var(--orange); flex: none;
  }
  .mascot-art {
    position: absolute; left: 200px; bottom: 0; width: 130px; height: 80px; z-index: 1;
    background: radial-gradient(ellipse at 60% 55%, #2e2e32 0%, #1b1b1e 75%);
    border-top-left-radius: 50px;
  }
  .contact {
    position: absolute; right: 30px; top: 150px; text-align: right; color: var(--white); z-index: 2;
  }
  .contact__name { font-size: 19px; font-weight: 700; line-height: 22px; }
  .contact__first { color: var(--orange); }
  .contact__last { color: var(--grey); }
  .contact__title { font-size: 11px; font-weight: 600; margin-bottom: 8px; }
  .contact__line {
    display: flex; justify-content: flex-end; align-items: center; gap: 6px;
    font-size: 11px; line-height: 17px;
  }
  .contact__line svg { width: 10px; height: 10px; fill: var(--orange); stroke: var(--orange); }
  .edge-tab {
    position: absolute; right: 0; top: 168px; width: 14px; height: 50px; background: var(--orange);
  }
  /* back */
  .card--back {
    background: linear-gradient(160deg, #f47330 0%, var(--orange) 60%, #e8611c 100%);
    display: flex; align-items: center; justify-content: center;
  }
  .card--back .brand {
    position: static; font-size: 30px; color: var(--orange-deep);
  }
</style>
</head>
<body>
<main class="stage">
  <section class="card card--front" aria-label="Card front">
    <div class="brand"><span class="brand__mark"></span>FALCRIDGE HIRES</div>

    <ul class="services">
      <li>Events</li>
      <li>Charity</li>
      <li>Concerts</li>
      <li>Weddings</li>
      <li>Sporting and Corp</li>
      <li>Luxury Restroom Trailers Rental and Sales</li>
    </ul>

    <div class="mascot-art" role="img" aria-label="Large dark tone-on-tone mascot illustration"></div>

    <div class="contact">
      <p class="contact__name"><span class="contact__first">Dwight</span> <span class="contact__last">Penner</span></p>
      <p class="contact__title">CFO</p>
      <p class="contact__line">555 318-0476
        <svg viewBox="0 0 10 10" aria-hidden="true"><path d="M2 1l2 2-1 1.3c.6 1.2 1.5 2.1 2.7 2.7L7 6l2 2-1.3 1.3C4.5 9 1 5.5.7 2.3z" stroke="none"/></svg></p>
      <p class="contact__line">info@website.com
        <svg viewBox="0 0 10 10" aria-hidden="true"><rect x="1" y="2" width="8" height="6" fill="none" stroke-width="1.2"/><path d="M1 2l4 3.3L9 2" fill="none" stroke-width="1.2"/></svg></p>
      <p class="contact__line">www.website.com
        <svg viewBox="0 0 10 10" aria-hidden="true"><circle cx="5" cy="5" r="4" fill="none" stroke-width="1.2"/><path d="M1 5h8M5 1c-2 2.5-2 5.5 0 8M5 1c2 2.5 2 5.5 0 8" fill="none" stroke-width=".9"/></svg></p>
    </div>
    <div class="edge-tab"></div>
  </section>

  <section class="card card--back" aria-label="Card back">
    <div class="brand"><span class="brand__mark"></span>FALCRIDGE HIRES</div>
  </section>
</main>
</body>
</html>
```